Pepper & Palm Business Card FUN & EXCITING

Here is the Information for the Card:
Jaswinder Bains (Ravi)
E: RaviBains@postlark.com
C: (480) 555-0147
www.PepperPalmLV.com

We don't want traditional Indian cliche, We a playful bold and fun business card.

Files: https://files.cloudvessel.net/share/folders/7TqRmXpZ2vKa9LwBn4YcHd3JsEf6UoGi?usp=share_link

https://files.cloudvessel.net/share/folders/4MzXaQ8rTw2YbNcVk6PsLe5GhJdR3FoU?usp=share_link

Target Market(s)

Las Vegas Local Restaurant

Industry/Entity Type

Indian Restaurant

Contact Information for Business Card

Name, Email, Cell Phone, Company Logo

```html
<!DOCTYPE html>
<html lang="en">
<head>
<meta charset="utf-8">
<title>Pepper &amp; Palm — Business Card</title>
<link href="https://fonts.googleapis.com/css2?family=Oswald:wght@500;700&family=Open+Sans:wght@400;600&display=swap" rel="stylesheet">
<style>
  :root {
    --page: #ece8e3;
    --card: #0e0e0e;
    --card-sheen: #1c1c1c;
    --pink: #e3256b;
    --yellow: #f5c518;
    --teal: #1fb39a;
    --white: #ffffff;
    --food-warm: #c8772e;
    --food-light: #e9ddc6;
  }
  * { box-sizing: border-box; margin: 0; padding: 0; }
  html, body {
    width: 1200px; height: 780px; overflow: hidden;
    background: var(--page);
  }
  .canvas { position: relative; width: 1200px; height: 780px; }

  .card {
    position: absolute;
    width: 560px; height: 320px;
    background: linear-gradient(135deg, var(--card-sheen) 0%, var(--card) 55%);
    overflow: hidden;
    box-shadow: 0 10px 24px rgba(0,0,0,.25);
  }
  .card--front { left: 100px; top: 50px; }
  .card--back  { left: 540px; top: 410px; }

  .wordmark {
    font-family: "Oswald", sans-serif;
    font-weight: 700;
    color: var(--pink);
    text-transform: uppercase;
    letter-spacing: 1px;
    line-height: 1;
  }
  .card--front .wordmark {
    position: absolute; left: 0; right: 0; top: 120px;
    text-align: center; font-size: 64px;
  }

  .food-photo {
    position: absolute; left: 0; top: 0; bottom: 0; width: 210px;
    background: linear-gradient(160deg, var(--food-warm) 0%, #9b4a1f 40%, var(--food-light) 75%, #d9cbb0 100%);
  }

  .card--back .wordmark {
    position: absolute; right: 60px; top: 38px;
    font-size: 48px; text-align: center; line-height: 1.02;
  }
  .accent-bar {
    position: absolute; right: 0; top: 160px;
    width: 14px; height: 26px; background: var(--yellow);
  }
  .holder-name {
    position: absolute; right: 40px; top: 160px;
    font-family: "Oswald", sans-serif; font-weight: 500;
    font-size: 24px; color: var(--yellow); text-transform: uppercase;
    letter-spacing: .5px;
  }
  .contact-list {
    position: absolute; right: 24px; top: 204px;
    list-style: none;
    font-family: "Open Sans", sans-serif; font-size: 14px; color: var(--white);
  }
  .contact-list li {
    display: flex; justify-content: flex-end; align-items: center;
    gap: 8px; height: 24px;
  }
  .contact-icon { width: 14px; height: 14px; fill: none; stroke: var(--teal); stroke-width: 2; }
</style>
</head>
<body>
<main class="canvas">

  <section class="card card--front" aria-label="Card front">
    <div class="wordmark">Pepper &amp; Palm</div>
  </section>

  <section class="card card--back" aria-label="Card back">
    <div class="food-photo" role="img" aria-label="Overhead photo of trays of curries, rice, crisps and dipping sauces"></div>

    <div class="wordmark">Pepper &amp;<br>Palm</div>
    <span class="accent-bar"></span>

    <h1 class="holder-name">Jaswinder Bains (Ravi)</h1>

    <ul class="contact-list">
      <li>(480) 555-0147
        <svg class="contact-icon" viewBox="0 0 16 16" aria-hidden="true"><path d="M3 2l3 1 1 3-2 1.5a9 9 0 0 0 3.5 3.5L10 9l3 1 1 3-2 1.5C7 14 2 9 1.5 4z"/></svg>
      </li>
      <li>RaviBains@postlark.com
        <svg class="contact-icon" viewBox="0 0 16 16" aria-hidden="true"><rect x="1.5" y="3.5" width="13" height="9"/><path d="M1.5 3.5L8 9l6.5-5.5"/></svg>
      </li>
      <li>www.PepperPalmLV.com
        <svg class="contact-icon" viewBox="0 0 16 16" aria-hidden="true"><circle cx="8" cy="8" r="6.5"/><path d="M1.5 8h13M8 1.5c-3 3.5-3 9.5 0 13M8 1.5c3 3.5 3 9.5 0 13"/></svg>
      </li>
    </ul>
  </section>

</main>
</body>
</html>
```